Mobile Disc Jockey Service Brochure

We are looking for a brochure to showcase our Mobile DJ Business. It needs to be something professional looking and fit our target market of Weddings. We cater to events of all types but majority of our clients are brides looking for professional service at affordable prices.

Our website for reference: http://www.theclefcart.com/
facebook for reference: https://www.facebook.com/MarcusClefCart

I've uploaded a picture of us, our logo and some other photos that might be useful. Feel free to use additional stock photos that may be applicable to our project needs. Feel free to crop photos as necessary

I'd like this to be an 8 1/2" x 11" bifold, or trifold brochure, double sided. The front can be simple with our logo and phone number. Back can also be simple with a small logo and our website. I'd like one of the areas to focus on our bio and picture, and the other areas can describe our packages and what we offer as well as our mission statement

Some other information: We provide not only Professional and Enthusiastic DJ Services but we also do Uplighting as well as Event planning.

Target Market(s)

Weddings, Anniversary Parties, Birthdays, Themed Party

Industry/Entity Type

Business

Requirements
Must have
• Something describing our services like the following (feel free to rearrange the wording if necessary).
• All packages are hourly and custom built to fit your party needs. A list of our offerings includes:
• Cocktail music, dinner music, dance music
• Ultimate coordination of activities and unique event planning experience
• HD Sound
• LED Light Show
• Wireless Microphone System
• Unlimited choice of song titles from Digital to Vinyl
• Free travel within 50 miles - Travel outside of this is calculated with a fee per additional mile.
• Optional Services:
• Projector with Screen for Slide Shows & Movies
• Uplighting
• We provide a Fun & Easy to use web interface that walks you through the timeline of your event capturing every detail you desire, making planning fun! We guarantee you will hear everything you want, we have an endless music library as well as mobile internet so we can access any song you and your guests want instantly! In addition to the Online Event Planner, we offer unlimited consultations prior to your event to ensure face to face that you are getting everything you want and more.
• I'd like to see something featuring our services as well as our picture that I uploaded maybe cropped at the chest level or there abouts with this information:
• We are a husband and wife team. Marcus Holloway, the DJ has been providing custom soundtracks for events of all types for well over a decade. In 2011 his wife Tessa joined the team to handle all of the event coordination and logistics. Together we run the Clef Cart offering Professional DJ Services at a personal level. We enjoy working with clients to create the event that they deserve at an affordable price. Contact us today for your quote or visit us online.
• (555) 314-2286
• theclefcart@mailvo.com
• www.theclefcart.com
• www.facebook.com/MarcusClefCart
• Id also like something along the lines of:
• Your choice of DJ can make or break your event. The Clef Cart guarantees to go above and beyond to make your event flawless and unforgettable. We promise to provide nothing but the best, well within your budget. When it comes to Weddings, we recognize that your Wedding is the most important day of your life! We will work with you side by side to ensure that it's everything you have dreamed of and more. Let the experience we provide create a beautiful memory that will last a lifetime.
• (Mission Statement)
• Our mission is to provide high quality and affordable mobile DJ services that will fill your event with beautiful lifelong memories.
Nice to have
• Id like to see the picture of the bride and grandfather dancing put in there somewhere.
• Color Scheme should be a mix of greys, black, white, you can add color as needed to match photos/logo, etc.

```html
<!DOCTYPE html>
<html lang="en">
<head>
<meta charset="utf-8">
<title>The Clef Cart – Brochure Inside Spread</title>
<link rel="stylesheet" href="https://fonts.googleapis.com/css2?family=Maven+Pro:wght@400;500;700&family=Open+Sans:wght@400;700&family=Arimo&display=swap">
<style>
  :root {
    --red: #bf1a0a;
    --grey: #dfe2e2;
    --grey-dark: #d3d7d7;
    --ink: #231f20;
    --white: #ffffff;
    --photo-dark: #2a2630;
    --photo-mid: #5a4a58;
  }
  * { margin: 0; padding: 0; box-sizing: border-box; }
  html, body { width: 1200px; height: 1000px; overflow: hidden; background: var(--white); }
  body { position: relative; font-family: "Open Sans", sans-serif; color: var(--ink); }
  .abs { position: absolute; }
  .spread-shapes { position: absolute; left: 0; top: 0; }
  .kicker { font-family: "Maven Pro", sans-serif; font-weight: 500; font-size: 13px; letter-spacing: 0.6px; line-height: 14px; }
  .headline { font-family: "Maven Pro", sans-serif; font-weight: 500; font-size: 18px; letter-spacing: 0.5px; line-height: 20px; }
  .on-red { color: var(--white); }
  .body-copy { font-size: 9px; line-height: 11.6px; width: 196px; }
  .body-copy p + p { margin-top: 6px; }
  .offering { position: absolute; width: 140px; text-align: center; }
  .offering svg { display: block; margin: 0 auto; }
  .offering-label { font-family: "Maven Pro", sans-serif; font-weight: 700; font-size: 9.5px; margin-top: 4px; letter-spacing: 0.2px; }
  .travel-note { left: 89px; top: 760px; width: 210px; font-size: 9px; line-height: 12px; }
  .travel-note p + p { margin-top: 8px; }
  .photo { position: absolute; background: linear-gradient(160deg, var(--photo-mid), var(--photo-dark)); }
  .avatar { position: absolute; width: 72px; height: 72px; border: 2px solid var(--white); background: linear-gradient(150deg, #b9a49a, #6d5a52); }
  .testimonial-quote { position: absolute; color: var(--white); font-size: 9px; line-height: 11.6px; width: 128px; }
  .testimonial-name { position: absolute; color: var(--white); font-size: 8px; line-height: 10px; }
  .testimonial-name strong { display: block; font-weight: 700; }
  .panel-caption { position: absolute; top: 857px; font-family: "Arimo", sans-serif; font-size: 17px; width: 300px; text-align: center; }
</style>
</head>
<body>

<svg class="spread-shapes" width="1200" height="1000" viewBox="0 0 1200 1000" aria-hidden="true">
  <!-- inside left -->
  <rect x="51" y="313" width="275" height="522" fill="var(--grey)"/>
  <polygon points="51,313 326,313 51,606" fill="var(--grey-dark)"/>
  <polygon points="51,124 490,124 330,313 51,313" fill="var(--red)"/>
  <!-- inside right -->
  <polygon points="600,124 700,124 866,313 600,313" fill="var(--red)"/>
  <polygon points="712,124 1149,124 1149,608 878,318" fill="var(--grey)"/>
  <rect x="600" y="689" width="549" height="146" fill="var(--red)"/>
</svg>

<!-- hero wedding photo -->
<svg class="abs" style="left:330px;top:124px" width="270" height="189" viewBox="0 0 270 189" role="img" aria-label="Photo of a bride and groom dancing on a forest path">
  <defs>
    <linearGradient id="forest" x1="0" y1="0" x2="0" y2="1">
      <stop offset="0" stop-color="#7fa046"/><stop offset="0.7" stop-color="#4f6e2c"/><stop offset="1" stop-color="#a48a6a"/>
    </linearGradient>
  </defs>
  <polygon points="166,0 270,0 270,189 6,189" fill="url(#forest)"/>
</svg>

<!-- offerings heading -->
<div class="abs on-red" style="left:89px;top:242px">
  <div class="kicker">A LIST OF OUR</div>
  <div class="headline">OFFERINGS</div>
  <div class="kicker">INCLUDES:</div>
</div>

<!-- offerings grid -->
<div class="offering" style="left:73px;top:330px">
  <svg width="40" height="38" viewBox="0 0 40 38"><g fill="none" stroke="var(--red)" stroke-width="2"><path d="M8 8h10l-3 12h-4z"/><path d="M13 20v12M9 33h8"/><path d="M22 8h10l-3 12h-4z"/><path d="M27 20v12M23 33h8"/></g></svg>
  <div class="offering-label">Cocktail music</div>
</div>
<div class="offering" style="left:190px;top:330px">
  <svg width="40" height="38" viewBox="0 0 40 38"><circle cx="20" cy="19" r="12" fill="var(--red)"/><circle cx="20" cy="19" r="7" fill="none" stroke="var(--white)" stroke-width="1.5"/><path d="M3 8v22M37 8v22" stroke="var(--red)" stroke-width="2.5"/></svg>
  <div class="offering-label">Dinner music</div>
</div>
<div class="offering" style="left:73px;top:405px">
  <svg width="40" height="46" viewBox="0 0 40 46" role="img" aria-label="Dancing couple icon"><rect x="8" y="4" width="26" height="38" rx="4" fill="var(--red)"/></svg>
  <div class="offering-label">Dance music</div>
</div>
<div class="offering" style="left:190px;top:413px">
  <svg width="40" height="38" viewBox="0 0 40 38"><rect x="5" y="6" width="30" height="28" rx="2" fill="var(--red)"/><g fill="var(--white)"><rect x="9" y="14" width="4" height="4"/><rect x="15" y="14" width="4" height="4"/><rect x="21" y="14" width="4" height="4"/><rect x="27" y="14" width="4" height="4"/><rect x="9" y="21" width="4" height="4"/><rect x="15" y="21" width="4" height="4"/><rect x="21" y="21" width="4" height="4"/><rect x="27" y="21" width="4" height="4"/><rect x="9" y="28" width="4" height="3"/><rect x="15" y="28" width="4" height="3"/></g></svg>
  <div class="offering-label">Event planning</div>
</div>
<div class="offering" style="left:73px;top:497px">
  <svg width="50" height="38" viewBox="0 0 50 38"><path d="M6 24a19 19 0 0 1 38 0" fill="none" stroke="var(--red)" stroke-width="3"/><rect x="3" y="20" width="8" height="14" rx="2" fill="var(--red)"/><rect x="39" y="20" width="8" height="14" rx="2" fill="var(--red)"/><text x="25" y="32" text-anchor="middle" font-family="Maven Pro, sans-serif" font-weight="700" font-size="13" fill="var(--red)">HD</text></svg>
  <div class="offering-label">HD Sound</div>
</div>
<div class="offering" style="left:190px;top:500px">
  <svg width="70" height="34" viewBox="0 0 70 34"><text x="35" y="30" text-anchor="middle" font-family="Maven Pro, sans-serif" font-weight="700" font-size="33" fill="none" stroke="var(--red)" stroke-width="2.5" stroke-dasharray="2 1.5">LED</text></svg>
  <div class="offering-label">LED Light Show</div>
</div>
<div class="offering" style="left:73px;top:572px">
  <svg width="44" height="42" viewBox="0 0 44 42"><circle cx="30" cy="11" r="8" fill="var(--red)"/><path d="M24 17L7 36" stroke="var(--red)" stroke-width="5" stroke-linecap="round"/></svg>
  <div class="offering-label">Wireless Microphone</div>
</div>
<div class="offering" style="left:190px;top:574px">
  <svg width="56" height="40" viewBox="0 0 56 40"><g stroke="var(--ink)" stroke-width="0.6"><path d="M2 10h52M2 16h52M2 22h52M2 28h52M2 34h52"/></g><g fill="var(--red)"><ellipse cx="9" cy="30" rx="4" ry="3"/><rect x="12" y="8" width="1.8" height="22"/><ellipse cx="42" cy="32" rx="4" ry="3"/><rect x="45" y="10" width="1.8" height="22"/></g><path d="M27 38c-4-6 6-12 2-24c-2-6-6 2-2 10c3 6 8 8 4 12c-3 2-8 0-6-4" fill="none" stroke="var(--red)" stroke-width="2"/></svg>
  <div class="offering-label">Unlimited of song</div>
</div>
<div class="offering" style="left:73px;top:667px">
  <svg width="50" height="36" viewBox="0 0 50 36"><rect x="4" y="8" width="42" height="22" rx="5" fill="var(--red)"/><circle cx="32" cy="19" r="7" fill="var(--white)"/><circle cx="32" cy="19" r="4" fill="var(--red)"/><path d="M10 15h10M10 19h10M10 23h10" stroke="var(--white)" stroke-width="1.5"/></svg>
  <div class="offering-label">Projector with Screen</div>
</div>
<div class="offering" style="left:190px;top:667px">
  <svg width="40" height="36" viewBox="0 0 40 36"><circle cx="20" cy="18" r="16" fill="var(--red)"/><g fill="var(--white)"><circle cx="14" cy="12" r="2"/><circle cx="21" cy="10" r="2"/><circle cx="27" cy="14" r="2"/><circle cx="12" cy="19" r="2"/><circle cx="19" cy="17" r="2"/><circle cx="26" cy="21" r="2"/><circle cx="16" cy="25" r="2"/><circle cx="23" cy="27" r="2"/></g></svg>
  <div class="offering-label">Uplighting</div>
</div>

<div class="abs travel-note">
  <p>Free travel*</p>
  <p>within 50 miles - Travel outside of this is calculated with a fee per additional mile.</p>
</div>

<!-- mission and copy -->
<div class="abs" style="left:362px;top:333px">
  <div class="kicker">MISSION</div>
  <div class="headline">STATEMENT</div>
  <div class="body-copy" style="margin-top:8px;width:200px">
    <p>Our mission is to provide high quality and affordable mobile DJ services that will fill your event with beautiful lifelong memories.</p>
  </div>
</div>
<div class="abs" style="left:361px;top:442px">
  <div class="kicker">MAKE YOUR EVENT</div>
  <div class="headline">MEMORALE</div>
  <div class="body-copy" style="margin-top:8px">
    <p>Your choice of DJ can make or break your event. The Clef Cart guarantees to go above and beyond to make your event flawless and unforgettable. We promise to provide nothing but the best, well within your budget.</p>
    <p>When it comes to Weddings, we recognize that your Wedding is the most important day of your life! We will work with you side by side to ensure that it's everything you have dreamed of and more. Let our experience create a memory for a lifetime, you will not be disappointed!</p>
    <p>We provide a Fun &amp; Easy to use web interface that walks you through the timeline of your event capturing every detail you desire, making planning fun! We guarantee you will hear everything you want, we have an endless music library as well as mobile internet so we can access any song you and your guests want instantly!</p>
    <p>In addition to the Online Event Planner, we offer unlimited consultations prior to your event to ensure face to face that you are getting everything you want and more.</p>
  </div>
</div>

<!-- photo gallery -->
<div class="abs on-red" style="left:640px;top:242px">
  <div class="kicker">PHOTO</div>
  <div class="headline">GALLERY</div>
</div>
<div class="photo" role="img" aria-label="Photo of a bride dancing with her grandfather" style="left:879px;top:184px;width:147px;height:193px"></div>
<div class="photo" role="img" aria-label="Photo of a bride dancing with guests in a hall" style="left:697px;top:326px;width:172px;height:131px;background:linear-gradient(160deg,#8a8478,#3a3632)"></div>
<div class="photo" role="img" aria-label="Photo of couples on a dance floor" style="left:640px;top:467px;width:229px;height:154px"></div>
<div class="photo" role="img" aria-label="Photo of the DJ booth with balloons at a reception" style="left:879px;top:387px;width:230px;height:140px;background:linear-gradient(160deg,#7a6a70,#2e2830)"></div>
<div class="photo" role="img" aria-label="Photo of colourful LED lights on a dance floor" style="left:881px;top:537px;width:202px;height:84px;background:linear-gradient(160deg,#4a6aa0,#2a2a50 60%,#7a4a8a)"></div>

<!-- testimonials -->
<div class="abs" style="left:640px;top:651px">
  <div class="kicker">CLIENT</div>
  <div class="headline">TESTIMONIALS</div>
</div>
<div class="avatar" role="img" aria-label="Portrait of client Darnell Pruitt" style="left:639px;top:699px"></div>
<div class="testimonial-quote" style="left:727px;top:702px">Thank you guys so much for coming out. My wife and our family had tons of fun and you and your wife make a really good team! Definitely will be referring you guys because you guys have skill and good personalities!</div>
<div class="testimonial-name" style="left:640px;top:780px"><strong>Darnell Pruitt</strong>October 30, 2014</div>
<div class="avatar" role="img" aria-label="Portrait of client Renee Calloway" style="left:877px;top:699px"></div>
<div class="testimonial-quote" style="left:965px;top:702px;width:130px">Hosted my mom party and did a great job my family was impressed. Thanks great times.</div>
<div class="testimonial-name" style="left:880px;top:780px"><strong>Renee Calloway</strong>June 4, 2014</div>

<div class="panel-caption" style="left:196px">Option 1_Inside Left</div>
<div class="panel-caption" style="left:748px">Option 1_Inside Right</div>

</body>
</html>
```